Business card design for Automotive workshop

We need a business card for a new automotive repair and tyre shop called Keelstone Prime Automotive located in New Zealand. We are a clean, modern and fresh workshop and company.

Front needs to feature logo,
my name:
Marlo Fenwicke (director)

Address:
48 Tarn Lane
Whitianga 3510

Phone: 07 594 2713
Mobile: 027 451 9362
Email: office@keelstoneautomotive.example.nz
Website: keelstoneautomotive.example.nz

Back needs to feature an area to write down appointment details, date and time.

Also feature a list of jobs and work we do such as,
Vehicle Servicing
All Mechanical Repairs
Warrant of Fitness
Tyres & Wheel Alignments
Automotive Diagnostics
Automotive Parts & Supplies

```html
<!DOCTYPE html>
<html lang="en">
<head>
<meta charset="utf-8">
<title>Keelstone Prime Automotive – Business Card</title>
<link rel="stylesheet" href="https://fonts.googleapis.com/css2?family=Open+Sans:wght@400;600;700&display=swap">
<style>
  :root {
    --card-dark: #2b2a2d;
    --brand-red: #e02127;
    --ink-light: #ffffff;
    --field-grey: #c9c9c9;
    --page-bg: #e9e7e4;
  }
  * { box-sizing: border-box; margin: 0; padding: 0; }
  html, body { width: 1200px; height: 835px; overflow: hidden; }
  body {
    background: var(--page-bg);
    font-family: "Open Sans", Arial, sans-serif;
    color: var(--ink-light);
    position: relative;
  }
  .card {
    position: absolute;
    left: 290px;
    width: 620px;
    height: 355px;
    background: var(--card-dark);
    border-radius: 20px;
    overflow: hidden;
    box-shadow: 0 6px 18px rgba(0,0,0,0.25);
  }
  .card--front { top: 45px; }
  .card--back { top: 435px; }

  /* Wordmark */
  .wordmark {
    position: absolute;
    display: flex;
    align-items: center;
    gap: 10px;
  }
  .wordmark__square { width: 14px; height: 14px; background: var(--brand-red); flex: none; }
  .wordmark__name {
    font-weight: 700;
    color: var(--ink-light);
    text-transform: uppercase;
    letter-spacing: 1.5px;
    line-height: 1.15;
  }
  .card--front .wordmark { left: 38px; top: 160px; }
  .card--front .wordmark__name { font-size: 19px; }
  .card--back .wordmark { left: 330px; top: 100px; }
  .card--back .wordmark__name { font-size: 20px; }

  /* Front: red divider */
  .divider { position: absolute; left: 0; top: 0; }
  .contact-name {
    position: absolute; left: 318px; top: 76px;
    font-size: 19px; font-weight: 700; color: var(--brand-red);
  }
  .contact-role {
    position: absolute; left: 318px; top: 102px;
    font-size: 12px;
  }
  .contact-address {
    position: absolute; left: 318px; top: 140px;
    font-size: 13.5px;
  }
  .contact-list {
    position: absolute; left: 318px; top: 196px;
    list-style: none; font-size: 13.5px; line-height: 22px;
  }

  /* Back */
  .back-shape { position: absolute; left: 0; top: 0; }
  .services {
    position: absolute; left: 44px; top: 86px;
    list-style: none; font-size: 14px; line-height: 39px;
  }
  .appointment {
    position: absolute; right: 30px; top: 210px;
    display: grid; grid-template-columns: auto 120px; gap: 18px 10px;
    align-items: center; font-size: 15px;
  }
  .appointment__label { text-align: right; }
  .appointment__field {
    height: 22px; border-radius: 11px; background: var(--field-grey);
  }
</style>
</head>
<body>

<section class="card card--front" aria-label="Business card front">
  <svg class="divider" width="620" height="355" viewBox="0 0 620 355" aria-hidden="true">
    <rect x="280" y="-20" width="16" height="150" rx="8" fill="var(--brand-red)"/>
    <circle cx="288" cy="110" r="3" fill="#fff"/>
    <path d="M283 121 a5 5 0 0 1 10 0 z" fill="#fff"/>
    <rect x="280" y="178" width="16" height="200" rx="8" fill="var(--brand-red)"/>
    <!-- mobile -->
    <rect x="284" y="201" width="8" height="12" rx="1.5" fill="none" stroke="#fff" stroke-width="1.5"/>
    <!-- phone -->
    <path d="M283 229 h10 v7 h-10 z M285 229 v-2 h6 v2" fill="none" stroke="#fff" stroke-width="1.5"/>
    <!-- envelope -->
    <rect x="283" y="248" width="10" height="8" fill="none" stroke="#fff" stroke-width="1.4"/>
    <path d="M283 248 l5 4 l5 -4" fill="none" stroke="#fff" stroke-width="1.2"/>
    <!-- globe -->
    <circle cx="288" cy="274" r="5" fill="none" stroke="#fff" stroke-width="1.4"/>
    <path d="M283 274 h10 M288 269 v10" stroke="#fff" stroke-width="1"/>
  </svg>

  <div class="wordmark">
    <span class="wordmark__square"></span>
    <span class="wordmark__name">Keelstone Prime<br>Automotive</span>
  </div>

  <h1 class="contact-name">Marlo Fenwicke</h1>
  <p class="contact-role">Managing Director</p>
  <p class="contact-address">48 Tarn Lane, Whitianga 3510</p>
  <ul class="contact-list">
    <li>+ 027 451 9362</li>
    <li>+ 07 594 2713</li>
    <li>office@keelstoneautomotive.example.nz</li>
    <li>keelstoneautomotive.example.nz</li>
  </ul>
</section>

<section class="card card--back" aria-label="Business card back">
  <svg class="back-shape" width="620" height="355" viewBox="0 0 620 355" aria-hidden="true">
    <path d="M0 0 H620 V72 H330 C300 72 290 40 255 40 H0 Z" fill="var(--brand-red)"/>
    <path d="M0 40 H22 V108 l8 8 l-8 8 V147 l8 8 l-8 8 V186 l8 8 l-8 8 V225 l8 8 l-8 8 V264 l8 8 l-8 8 V303 l8 8 l-8 8 V355 H0 Z" fill="var(--brand-red)"/>
  </svg>

  <ul class="services">
    <li>Vehicle Servicing</li>
    <li>All Mechanical Repairs</li>
    <li>Warrant of Fitness</li>
    <li>Tyres &amp; Wheel Alignments</li>
    <li>Automotive Diagnostics</li>
    <li>Automotive Parts &amp; Supplies</li>
  </ul>

  <div class="wordmark">
    <span class="wordmark__square"></span>
    <span class="wordmark__name">Keelstone Prime<br>Automotive</span>
  </div>

  <div class="appointment">
    <span class="appointment__label">Date</span><span class="appointment__field"></span>
    <span class="appointment__label">Time</span><span class="appointment__field"></span>
  </div>
</section>

</body>
</html>
```